Corbell Lending Partners - Real estate loans - need a business card with a logo

I need a logo and a business card that looks elegant - that looks as if it is a big stablish corporation - We do real estate loans, my goal is to brand myself with colors black background - gold or silver letters - some combination - Name of the company different color than the rest of the card -

```html
<!DOCTYPE html>
<html lang="en">
<head>
<meta charset="UTF-8">
<title>Corbell Lending Partners – Business Card</title>
<link href="https://fonts.googleapis.com/css2?family=Michroma&family=Montserrat:wght@400;600&display=swap" rel="stylesheet">
<style>
  :root {
    --backdrop: #161616;
    --card: #1f1f1f;
    --card-edge: #262626;
    --gold: #c9a86a;
    --silver: #bdbdbd;
    --white: #f2f2f2;
  }
  * { box-sizing: border-box; margin: 0; padding: 0; }
  html, body {
    width: 1200px; height: 900px; overflow: hidden;
    background: var(--backdrop);
  }
  .canvas {
    width: 1200px; height: 900px;
    display: flex; flex-direction: column; align-items: center; justify-content: center;
    gap: 40px;
  }
  .card {
    position: relative;
    width: 700px; height: 400px;
    background: linear-gradient(135deg, var(--card-edge), var(--card));
    border-bottom: 4px solid var(--gold);
    box-shadow: 0 18px 40px rgba(0,0,0,.55);
  }
  .brand {
    font-family: "Michroma", sans-serif;
    font-weight: 400;
    letter-spacing: 2px;
    text-transform: uppercase;
  }
  .brand-mark {
    display: inline-block;
    width: 22px; height: 22px;
    background: var(--gold);
    flex: none;
  }
  /* Front */
  .card-front {
    display: flex; align-items: center; justify-content: center; gap: 18px;
  }
  .card-front .brand {
    color: var(--silver);
    font-size: 30px;
    line-height: 1.25;
    text-align: left;
  }
  /* Back */
  .card-back {
    display: flex; align-items: center;
    padding: 0 50px;
  }
  .back-brand {
    width: 290px;
    display: flex; align-items: center; gap: 14px;
  }
  .back-brand .brand {
    color: var(--white);
    font-size: 21px;
    line-height: 1.3;
  }
  .divider {
    width: 2px; height: 200px;
    background: var(--gold);
    margin: 0 40px 0 30px;
  }
  .contact {
    font-family: "Montserrat", sans-serif;
    color: var(--white);
    font-size: 17px;
    line-height: 1.35;
  }
  .contact-name {
    font-family: "Montserrat", sans-serif;
    font-weight: 600;
    color: var(--gold);
    font-size: 28px;
    letter-spacing: 1px;
    text-transform: uppercase;
  }
  .contact-role { margin-bottom: 14px; }
  .contact-address { margin-bottom: 12px; }
  .contact-line { display: flex; align-items: center; gap: 9px; }
  .contact-line svg { width: 13px; height: 13px; flex: none; }
</style>
</head>
<body>
<main class="canvas">
  <section class="card card-front">
    <span class="brand-mark"></span>
    <p class="brand">Corbell Lending<br>Partners</p>
  </section>

  <section class="card card-back">
    <div class="back-brand">
      <span class="brand-mark"></span>
      <p class="brand">Corbell Lending<br>Partners</p>
    </div>
    <div class="divider"></div>
    <div class="contact">
      <p class="contact-name">Daniel Reyes</p>
      <p class="contact-role">Founder</p>
      <p class="contact-address">418 Harlow Avenue<br>Brookfield, WA 99021</p>
      <p class="contact-line">
        <svg viewBox="0 0 16 16" fill="none" stroke="#c9a86a" stroke-width="1.6"><path d="M4 1.5l2.5 3-1.5 1.5c.8 2 2.5 3.7 4.5 4.5L11 9l3 2.5-1.5 2.5C7 13.5 2.5 9 2 3z"/></svg>
        555 013 4827
      </p>
      <p class="contact-line">
        <svg viewBox="0 0 16 16" fill="none" stroke="#c9a86a" stroke-width="1.6"><rect x="1.5" y="3.5" width="13" height="9"/><path d="M1.5 3.5L8 9l6.5-5.5"/></svg>
        info@corbelllending.com
      </p>
      <p class="contact-line">
        <svg viewBox="0 0 16 16" fill="none" stroke="#c9a86a" stroke-width="1.4"><circle cx="8" cy="8" r="6.3"/><ellipse cx="8" cy="8" rx="2.8" ry="6.3"/><path d="M1.7 8h12.6"/></svg>
        www.corbelllending.com
      </p>
    </div>
  </section>
</main>
</body>
</html>
```